High Tech Real Estate Startup needs a business card

We are developing an innovative real estate marketing product based around advanced search and virtual reality.

We talk to people, we need business cards.

Target Market(s)

The target market is technology professionals and realtors.

Contact Information for Business Card

The information to be included will include

Name
Title
Phone Number
E-mail Address
www.zelquin.com

It should use simple iconography for each one of those fields.

Font styles to use
Other font styles liked:
• Co, Jubilat, Avenir

Colors

Designer to choose colors to be used in the design.

Requirements
Must have
• Clean aesthetic,
• Good use of negative space.
• It should use our company logo, shown in the attached file. It is able to use the negative of that logo (coloured font and white background) and I have attached other acceptable accent colours in a swatch file.
Should not have
• Should not be too busy
• No extraneous text (slogans, tag lines etc)

```html
<!DOCTYPE html>
<html lang="en">
<head>
<meta charset="utf-8">
<title>Zelquin Business Card</title>
<link href="https://fonts.googleapis.com/css2?family=Oswald:wght@500&family=Work+Sans:wght@400;600&display=swap" rel="stylesheet">
<style>
  :root {
    --backdrop: #1c1c1d;
    --card: #1f1f20;
    --card-edge: #2a2a2b;
    --accent: #12b8bd;
    --text: #f2f2f2;
    --muted: #d9d9d9;
  }
  * { margin: 0; padding: 0; box-sizing: border-box; }
  html, body {
    width: 1200px; height: 900px; overflow: hidden;
    background: var(--backdrop);
    font-family: "Work Sans", Arial, sans-serif;
  }
  .canvas {
    width: 1200px; height: 900px;
    display: flex; flex-direction: column; align-items: center; justify-content: center;
    gap: 36px;
  }
  .card {
    position: relative;
    width: 690px; height: 394px;
    background: linear-gradient(135deg, var(--card) 0%, #232324 60%, #1b1b1c 100%);
    border: 1px solid var(--card-edge);
    box-shadow: 0 10px 26px rgba(0,0,0,.5);
  }
  /* Front */
  .brand-mark {
    position: absolute; left: 50%; top: 50%;
    width: 176px; height: 146px;
    transform: translate(-50%, -50%);
    background: var(--accent);
    display: flex; align-items: center; justify-content: center;
  }
  .brand-name {
    font-family: "Work Sans", Arial, sans-serif;
    font-weight: 600; font-size: 22px; letter-spacing: 1.5px;
    color: #ffffff;
  }
  /* Back */
  .identity {
    position: absolute; right: 378px; top: 150px;
    text-align: right;
  }
  .person-name {
    font-family: "Oswald", "Arial Narrow", sans-serif;
    font-weight: 500; font-size: 38px; line-height: 1;
    color: var(--accent); letter-spacing: 0.3px;
  }
  .person-title {
    margin-top: 4px;
    font-size: 17px; color: var(--muted); letter-spacing: 0.6px;
  }
  .divider {
    position: absolute; left: 333px; top: 150px;
    width: 1.5px; height: 56px; background: var(--text);
  }
  .contacts {
    position: absolute; left: 356px; top: 150px;
    list-style: none;
  }
  .contacts li {
    display: flex; align-items: center; gap: 10px;
    font-size: 17px; line-height: 20px; color: var(--text); letter-spacing: 0.6px;
  }
  .contacts svg { width: 11px; height: 11px; flex: none; }
  .address {
    position: absolute; left: 160px; top: 318px;
    font-size: 17px; color: var(--text); letter-spacing: 0.8px;
  }
</style>
</head>
<body>
<main class="canvas">
  <section class="card card-front" aria-label="Card front">
    <div class="brand-mark"><span class="brand-name">ZELQUIN</span></div>
  </section>

  <section class="card card-back" aria-label="Card back">
    <div class="identity">
      <h1 class="person-name">DANIEL REYES</h1>
      <p class="person-title">Director</p>
    </div>
    <div class="divider"></div>
    <ul class="contacts">
      <li>
        <svg viewBox="0 0 12 12" aria-hidden="true"><path d="M3 1l2 2.5-1.2 1.2a6 6 0 003.5 3.5L8.5 7 11 9l-1.2 1.8C6 11 1 6 1.2 2.2z" fill="var(--accent)"/></svg>
        +1-555-014-2873
      </li>
      <li>
        <svg viewBox="0 0 12 12" aria-hidden="true"><rect x="1" y="2.5" width="10" height="7" fill="none" stroke="var(--accent)" stroke-width="1.2"/><path d="M1 3l5 3.5L11 3" fill="none" stroke="var(--accent)" stroke-width="1.2"/></svg>
        info@zelquin.com
      </li>
      <li>
        <svg viewBox="0 0 12 12" aria-hidden="true"><circle cx="6" cy="6" r="5" fill="none" stroke="var(--accent)" stroke-width="1.1"/><ellipse cx="6" cy="6" rx="2.2" ry="5" fill="none" stroke="var(--accent)" stroke-width="1"/><path d="M1 6h10" stroke="var(--accent)" stroke-width="1"/></svg>
        www.zelquin.com
      </li>
    </ul>
    <p class="address">4170 Alder Crest Rd. Franklin, TN 37064</p>
  </section>
</main>
</body>
</html>
```